National Sales - Pick Up Truck Dealer

We need a logo design for a new vehicle dealership based in Sydney, Australia. The business name is Coastal Iron Haulers Motor Co. We will be selling American 'trucks/pick up trucks' like KRV, Torvan, Blaxer, Morrow T420, Kenzo Raptors, Morrow T640 and the likes.

These vehicles are a luxury option and we would like the logo to be strong, luxurious and masculine.Colours will be black and red or black and blue with the option of grey and white.

Target Market(s)

Men

Industry/Entity Type

Car Dealer

Contact Information for Business Card

Dennis Harlowe
Managing Director
0412 639 274
den@qelvtrk.com.au

Level 5, Brindle Parkway
17 Pemberly Lane
Baulkham Hills
NSW
Australia
Licence No: MD493152

Back of the card

qelvtrk.com.au

Font styles to use
Sans Serif

Colors

Designer to choose colors to be used in the design.

Requirements
Must have
• The company logo that is in the attachments, you can choose from the three which one you would like to work with. Must have vehicle images ....Please look at the attachments as they show examples of what we like and also provides potential images. If you choose to put an image on the front even if it is just the front of the vehicle can you please use the Black KRV Sorrento. Must have all details from the business card details section front and back
Nice to have
• N/A
Should not have
• No cars or standard trucks, please refer to the attached images to understand the product . Should not have any new logos or branding. No other colours besides what is in the logo you choose.

```html
<!DOCTYPE html>
<html lang="en">
<head>
<meta charset="utf-8">
<title>Coastal Iron Haulers Motor Co – Business Card</title>
<link href="https://fonts.googleapis.com/css2?family=Oswald:wght@500;600&family=Arimo:wght@400&display=swap" rel="stylesheet">
<style>
  :root {
    --navy: #3b3b6e;
    --red: #c11f2f;
    --card-white: #f5f5f6;
    --backdrop: #e6e6ea;
    --ink-light: #ffffff;
  }
  * { box-sizing: border-box; margin: 0; padding: 0; }
  html, body {
    width: 1200px; height: 900px; overflow: hidden;
    background: var(--backdrop);
  }
  .card {
    position: absolute; left: 100px; top: 140px;
    width: 1000px; height: 620px;
    display: flex;
    box-shadow: 0 10px 30px rgba(0,0,0,0.15);
  }
  .card-contact {
    width: 448px; height: 100%;
    background: var(--navy);
    color: var(--ink-light);
    position: relative;
    font-family: "Arimo", Arial, sans-serif;
  }
  .card-divider { width: 11px; background: var(--red); }
  .card-brand {
    flex: 1; background: var(--card-white);
    display: flex; align-items: center; justify-content: center;
  }
  .holder-name {
    position: absolute; right: 49px; top: 86px;
    font-family: "Oswald", sans-serif; font-weight: 600;
    font-size: 37px; letter-spacing: 0.2px; line-height: 1;
    white-space: nowrap;
  }
  .holder-title {
    position: absolute; right: 49px; top: 131px;
    font-size: 27px; line-height: 1; white-space: nowrap;
  }
  .contact-list {
    position: absolute; right: 49px; top: 283px;
    list-style: none;
  }
  .contact-list li {
    display: flex; align-items: center; justify-content: flex-end;
    gap: 8px; font-size: 27px; height: 37px; white-space: nowrap;
  }
  .contact-list svg { width: 21px; height: 21px; fill: var(--ink-light); flex: none; }
  .address {
    position: absolute; right: 49px; top: 414px;
    font-size: 24px; line-height: 34px; font-style: normal;
    text-align: right; white-space: nowrap;
  }
  .address span { display: block; }
  .brand-mark { display: flex; align-items: center; gap: 14px; }
  .brand-square { width: 22px; height: 22px; background: var(--red); flex: none; }
  .brand-name {
    font-family: "Oswald", sans-serif; font-weight: 500;
    font-size: 31px; color: var(--navy); text-transform: uppercase;
    letter-spacing: 0.3px; white-space: nowrap;
  }
</style>
</head>
<body>
  <section class="card">
    <div class="card-contact">
      <h1 class="holder-name">DENNIS HARLOWE</h1>
      <p class="holder-title">Managing Director</p>
      <ul class="contact-list">
        <li>0412 639 274
          <svg viewBox="0 0 24 24" aria-hidden="true"><path d="M7 1h10a2 2 0 0 1 2 2v18a2 2 0 0 1-2 2H7a2 2 0 0 1-2-2V3a2 2 0 0 1 2-2zm0 3v14h10V4zm5 15.5a1.2 1.2 0 1 0 0 2.4 1.2 1.2 0 0 0 0-2.4z"/></svg>
        </li>
        <li>den@qelvtrk.com.au
          <svg viewBox="0 0 24 24" aria-hidden="true"><path d="M2 5h20v14H2zm2 2v.5l8 5.5 8-5.5V7zm0 3v7h16v-7l-8 5.5z"/></svg>
        </li>
        <li>qelvtrk.com.au
          <svg viewBox="0 0 24 24" aria-hidden="true"><path d="M12 2a10 10 0 1 0 0 20 10 10 0 0 0 0-20zm0 2c1.3 1.6 2.2 3.8 2.4 7H9.6C9.8 7.8 10.7 5.6 12 4zM4.1 11a8 8 0 0 1 4.2-6.1C7.6 6.6 7.2 8.7 7.1 11zm0 2h3c.1 2.3.5 4.4 1.2 6.1A8 8 0 0 1 4.1 13zm5.5 0h4.8c-.2 3.2-1.1 5.4-2.4 7-1.3-1.6-2.2-3.8-2.4-7zm7.3 0h3a8 8 0 0 1-4.2 6.1c.7-1.7 1.1-3.8 1.2-6.1zm0-2c-.1-2.3-.5-4.4-1.2-6.1a8 8 0 0 1 4.2 6.1z"/></svg>
        </li>
      </ul>
      <address class="address">
        <span>Level 5, Brindle Parkway</span>
        <span>17 Pemberly Lane, Baulkham Hills</span>
        <span>NSW, Australia</span>
        <span>Licence No: MD493152</span>
      </address>
    </div>
    <div class="card-divider"></div>
    <div class="card-brand">
      <div class="brand-mark">
        <span class="brand-square"></span>
        <span class="brand-name">Coastal Iron Haulers Motor Co</span>
      </div>
    </div>
  </section>
</body>
</html>
```